Business Card for beauty technology startup

Design Glimora Business Card for a Beauty, based on the website identity and colors (https://www.glimora-example.com).
Glimora is a beauty tech startup that gathers helpful product info for beauty lovers and consumers (such as availability on stores, price range and product reviews) for makeup products. The card design must be young, colorful but clean, and very modern.

Target Market(s)

woman, 15-35

Industry/Entity Type

Cosmetics

Contact Information for Business Card

Full Name, address, phone

Font styles to use
Other font styles liked:
• Advent Pro

Colors
e34297
86cfc6
ffffff
5c5c5c
e8e8e8
e667a6
b2b2b2

Requirements
Must have
• One full colored side with a creative design and another with card info
• Use Color palette: #95C5C5 and/or #D38AA5
• Use fonts: Advent Pro
• Use website identity: https://www.glimora-example.com
Nice to have
• If needed extra font: Roboto

```html
<!DOCTYPE html>
<html lang="en">
<head>
<meta charset="utf-8">
<title>Glimora Business Card</title>
<link rel="stylesheet" href="https://fonts.googleapis.com/css2?family=Advent+Pro:wght@300;400&family=Montserrat:wght@600&family=Open+Sans:wght@400&display=swap">
<style>
  :root {
    --teal: #2bbdb2;
    --teal-dark: #1f9e95;
    --charcoal: #3c3c3e;
    --paper: #f4f4f2;
    --ink: #222222;
    --backdrop: #e8e8e8;
  }
  * { margin: 0; padding: 0; box-sizing: border-box; }
  html, body { width: 1200px; height: 1021px; overflow: hidden; }
  body { background: var(--backdrop); position: relative; font-family: "Open Sans", sans-serif; }

  .card {
    position: absolute;
    width: 560px;
    height: 320px;
    border-bottom: 6px solid var(--teal);
    border-right: 6px solid var(--teal-dark);
  }
  .card--front { left: 70px; top: 150px; background: var(--paper); }
  .card--back { left: 570px; top: 560px; background: var(--charcoal); }

  .brand { position: absolute; display: flex; align-items: center; color: var(--teal); font-family: "Advent Pro", sans-serif; font-weight: 300; letter-spacing: 0.14em; }
  .brand__dot { border: 2px solid var(--teal); border-radius: 50%; }
  .card--front .brand { right: 44px; top: 40px; font-size: 34px; gap: 12px; }
  .card--front .brand__dot { width: 40px; height: 40px; }

  .socials { position: absolute; right: 56px; top: 100px; display: flex; gap: 22px; }
  .socials span { width: 12px; height: 12px; background: var(--teal); border-radius: 2px; }

  .identity { position: absolute; left: 36px; top: 150px; padding-left: 16px; border-left: 12px solid var(--teal); }
  .identity__name { font-family: "Montserrat", sans-serif; font-weight: 600; font-size: 22px; color: var(--ink); line-height: 1.1; }
  .identity__title { font-family: "Advent Pro", sans-serif; font-size: 16px; color: var(--teal); }

  .contact { position: absolute; left: 52px; bottom: 36px; font-size: 13px; color: var(--ink); line-height: 1.45; }
  .contact__row { display: flex; gap: 10px; align-items: flex-start; }
  .contact__row svg { margin-top: 3px; flex: none; }

  .web { position: absolute; right: 40px; bottom: 120px; font-family: "Advent Pro", sans-serif; font-size: 17px; color: var(--teal); letter-spacing: 0.04em; }

  .card--back .brand { left: 50%; top: 110px; transform: translateX(-50%); font-size: 58px; gap: 20px; }
  .card--back .brand__dot { width: 64px; height: 64px; }
  .card--back .web { right: auto; left: 50%; bottom: 80px; transform: translateX(-50%); font-size: 18px; }
</style>
</head>
<body>
  <section class="card card--front">
    <div class="brand"><span class="brand__dot"></span>GLIMORA</div>
    <div class="socials"><span></span><span></span><span></span><span></span></div>
    <div class="identity">
      <div class="identity__name">Your Name</div>
      <div class="identity__title">Job Title</div>
    </div>
    <div class="web">www.glimora-example.com</div>
    <div class="contact">
      <div class="contact__row">
        <svg width="12" height="12" viewBox="0 0 24 24"><path fill="#2bbdb2" d="M6.6 10.8a15 15 0 0 0 6.6 6.6l2.2-2.2a1 1 0 0 1 1-.25 11 11 0 0 0 3.6.6 1 1 0 0 1 1 1V20a1 1 0 0 1-1 1A17 17 0 0 1 3 4a1 1 0 0 1 1-1h3.5a1 1 0 0 1 1 1 11 11 0 0 0 .6 3.6 1 1 0 0 1-.25 1z"/></svg>
        <span>000 000 0000</span>
      </div>
      <div class="contact__row">
        <svg width="12" height="14" viewBox="0 0 24 28"><path fill="#2bbdb2" d="M12 0a9 9 0 0 0-9 9c0 7 9 19 9 19s9-12 9-19a9 9 0 0 0-9-9zm0 12.5A3.5 3.5 0 1 1 12 5.5a3.5 3.5 0 0 1 0 7z"/></svg>
        <span>1480 Harbor View Ave, suite 210<br>Lakeside, Texas 75000</span>
      </div>
    </div>
  </section>

  <section class="card card--back">
    <div class="brand"><span class="brand__dot"></span>GLIMORA</div>
    <div class="web">www.glimora-example.com</div>
  </section>
</body>
</html>
```